Custom Cabinet Shop Needs a website design

Hi,
We need a website for a Custom Cabinet Shop and Cabinet parts manufacturing business.
The business has two sides to it. One side provides custom Kitchens, vanities, entertainment units, offices and what not to homeowners and contractors.
The 2nd side of the business provides built to order cabinet boxes and other parts required to put together a project to other cabinet shops, small contractors looking to install there own cabinets.
Website will need a Gallery to display work.
Color scheme to go well with logo.
current website is www.brambleoakcustomcabinets.com
being changed to www.brambleoak.ca
Logo Included in attached files.
Tagline "Joinery with Spirit"
Mission Statement "Our passion is to deliver inspired cabinetry solutions to suit all your needs, supported by our phenomenal star class customer service"
The website should convey quality and professionalism.
Thank you.
Homeowners/ Contractors
Entertainment

```html
<!DOCTYPE html>
<html lang="en">
<head>
<meta charset="utf-8">
<title>Brambleoak Custom Cabinets</title>
<link href="https://fonts.googleapis.com/css2?family=Open+Sans:wght@400;600;700&display=swap" rel="stylesheet">
<style>
:root{
  --orange:#e8471c;
  --black:#0a0a0a;
  --ink:#1a1a1a;
  --text:#444;
  --muted:#666;
  --band:#f4f4f4;
  --tab:#a3a3a3;
  --footer:#1c1c1c;
  --footer-text:#d0d0d0;
  --white:#fff;
}
*{margin:0;padding:0;box-sizing:border-box}
html,body{width:742px;height:1200px;overflow:hidden}
body{font-family:"Open Sans",Arial,sans-serif;background:var(--white);color:var(--text);position:relative}

/* header */
.site-header{position:absolute;left:0;top:0;width:742px;height:67px;background:var(--white)}
.brand{position:absolute;left:36px;top:22px;display:flex;align-items:center;gap:7px}
.brand-mark{width:22px;height:22px;background:var(--orange);border-radius:50%}
.brand-name{font-size:15px;font-weight:700;color:var(--ink);letter-spacing:.5px}
.main-nav{position:absolute;top:27px;left:439px;display:flex;font-size:9.6px;color:#333}
.main-nav a{text-decoration:none;color:inherit;height:15px;line-height:15px;display:block}
.main-nav .active{background:var(--orange);color:var(--white);width:45px;text-align:center}
.main-nav .n-gallery{margin-left:14px}
.main-nav .n-services,.main-nav .n-warranty,.main-nav .n-contact{margin-left:24px}

/* hero */
.hero{position:absolute;left:0;top:67px;width:742px;height:374px;
  background:linear-gradient(180deg,#3a2a1c 0%,#6b4a2e 40%,#4a3020 70%,#2a1a10 100%)}
.hero-glow{position:absolute;left:0;top:0;width:742px;height:374px;
  background:radial-gradient(ellipse at 45% 45%,rgba(220,160,90,.45),rgba(0,0,0,0) 60%)}
.slide-arrow{position:absolute;top:173px;width:30px;height:32px;display:flex;align-items:center;justify-content:center}
.slide-arrow.prev{left:0;background:rgba(232,71,28,.7)}
.slide-arrow.next{right:0;background:rgba(20,20,20,.8)}
.tagline{position:absolute;left:46px;top:304px;width:205px;height:34px;background:rgba(232,71,28,.85);
  color:var(--white);font-size:18.5px;line-height:34px;padding-left:15px;font-weight:400}

/* headings */
.section-title{font-size:17.5px;font-weight:700;color:var(--ink);letter-spacing:.3px}
.section-title span{color:var(--orange)}

/* mission */
.mission-title{position:absolute;top:456px;width:742px;text-align:center}
.mission-text{position:absolute;top:487px;left:66px;width:610px;text-align:center;font-size:11.4px;line-height:16px;color:#555}

/* services */
.services-band{position:absolute;left:0;top:553px;width:742px;height:155px;background:var(--band)}
.services-title{position:absolute;left:37px;top:36px}
.services-intro{position:absolute;left:37px;top:66px;width:195px;font-size:8px;line-height:10.7px;color:var(--muted)}
.service-card{position:absolute;top:28px;width:229px;height:100px;color:var(--white)}
.service-card.residential{left:246px;background:var(--orange)}
.service-card.business{left:475px;background:var(--black)}
.service-icon{position:absolute;left:12px;top:24px}
.service-card.business .service-icon{left:15px;top:22px}
.service-card h3{position:absolute;left:70px;top:16px;font-size:14px;font-weight:700;letter-spacing:.4px}
.service-card p{position:absolute;left:70px;top:43px;width:150px;font-size:7.8px;line-height:10.4px}
.read-more{position:absolute;right:14px;top:78px;font-size:8px;display:flex;align-items:center;gap:5px}
.read-more svg{display:block}

/* works */
.works-title{position:absolute;top:732px;width:742px;text-align:center}
.filter-tabs{position:absolute;top:763px;left:263px;display:flex;gap:3px;font-size:9.6px;color:var(--white)}
.filter-tabs span{height:16px;line-height:16px;text-align:center;background:var(--tab)}
.filter-tabs .active{background:var(--orange);width:37px}
.filter-tabs .t-res,.filter-tabs .t-bus{width:86px}
.work{position:absolute;width:161px;height:107px}
.work.feature{background:var(--orange);color:var(--white);text-align:center}
.work.feature h4{font-size:11px;font-weight:600;margin-top:30px}
.work.feature p{font-size:6.6px;margin-top:3px}
.work.feature .plus{margin-top:6px}
.work.feature .fold{position:absolute;right:0;bottom:0}
.pager{position:absolute;top:1042px;left:362px;display:flex;gap:4px}
.pager i{width:4px;height:4px;border-radius:50%;background:#c8c8c8;display:block}
.pager i.on{background:var(--orange)}

/* footer */
.site-footer{position:absolute;left:0;top:1078px;width:742px;height:122px;background:var(--footer);color:var(--footer-text)}
.footer-nav{position:absolute;left:37px;top:25px;display:flex;align-items:center;font-size:8px}
.footer-nav .home{border:1px solid #ccc;border-radius:9px;height:18px;line-height:16px;padding:0 18px;color:#eee}
.footer-nav .sep{margin:0 9px;color:#aaa}
.footer-nav .gallery{margin-left:11px}
.social{position:absolute;right:46px;top:25px;display:flex;gap:11px}
.social i{width:9px;height:9px;border-radius:50%;background:#e8e8e8;display:block}
.social-tip{position:absolute;left:642px;top:45px;background:var(--orange);color:var(--white);font-size:6.4px;font-weight:700;height:15px;line-height:15px;padding:0 6px;border-radius:8px}
.divider{position:absolute;left:37px;top:60px;width:668px;height:1px;background:#3a3a3a}
.contact-item{position:absolute;top:74px;display:flex;align-items:center;gap:8px;font-size:6.8px;line-height:9.8px}
.contact-item .ico{width:15px;height:15px;border-radius:50%;background:#f0f0f0;display:flex;align-items:center;justify-content:center;flex:none}
.copyright{position:absolute;right:30px;top:84px;font-size:7.4px}
</style>
</head>
<body>

<header class="site-header">
  <div class="brand"><span class="brand-mark"></span><span class="brand-name">BRAMBLEOAK</span></div>
  <nav class="main-nav">
    <a class="active" href="#">Home</a>
    <a class="n-gallery" href="#">Gallery</a>
    <a class="n-services" href="#">Services</a>
    <a class="n-warranty" href="#">Warranty</a>
    <a class="n-contact" href="#">Contact</a>
  </nav>
</header>

<section class="hero" role="img" aria-label="Photo of a dark-cabinet basement bar with live-edge counter, pendant lights and bar stools">
  <div class="hero-glow"></div>
  <div class="slide-arrow prev"><svg width="8" height="12" viewBox="0 0 8 12"><path d="M6 1L1 6l5 5" stroke="#fff" stroke-width="2" fill="none"/></svg></div>
  <div class="slide-arrow next"><svg width="8" height="12" viewBox="0 0 8 12"><path d="M2 1l5 5-5 5" stroke="#fff" stroke-width="2" fill="none"/></svg></div>
  <div class="tagline">Joinery with Spirit</div>
</section>

<h2 class="section-title mission-title">OUR <span>MISSION</span></h2>
<p class="mission-text">Our passion is to deliver inspired cabinetry solutions to suit all your needs, supported by our phenomenal star class customer service</p>

<section class="services-band">
  <h2 class="section-title services-title">OUR <span>SERVICES</span></h2>
  <p class="services-intro">Lorem ipsum dolor sit amet, consectetur adipiscing elit. Morbi ante risus, scelerisque sed sem id, accumsan tincidunt ligula. Integer gravida nunc fringilla risus porta.</p>

  <div class="service-card residential">
    <svg class="service-icon" width="42" height="36" viewBox="0 0 42 36"><path d="M21 2L2 19h6v15h10v-10h6v10h10V19h6z" fill="#fff"/></svg>
    <h3>RESIDENTIAL</h3>
    <p>Here at Brambleoak Custom Cabinets we are proud to be involved in the custom cabinet market.</p>
    <div class="read-more">Read More <svg width="9" height="9" viewBox="0 0 10 10"><circle cx="5" cy="5" r="4.3" stroke="#fff" fill="none"/><path d="M5 2.5v5M2.5 5h5" stroke="#fff"/></svg></div>
  </div>

  <div class="service-card business">
    <svg class="service-icon" width="32" height="40" viewBox="0 0 32 40"><rect x="1" y="1" width="30" height="38" fill="#fff"/><g fill="#000"><rect x="6" y="6" width="3" height="3"/><rect x="11" y="6" width="3" height="3"/><rect x="16" y="6" width="3" height="3"/><rect x="21" y="6" width="3" height="3"/><rect x="6" y="12" width="3" height="3"/><rect x="11" y="12" width="3" height="3"/><rect x="16" y="12" width="3" height="3"/><rect x="21" y="12" width="3" height="3"/><rect x="6" y="18" width="3" height="3"/><rect x="11" y="18" width="3" height="3"/><rect x="16" y="18" width="3" height="3"/><rect x="21" y="18" width="3" height="3"/><rect x="6" y="24" width="3" height="3"/><rect x="21" y="24" width="3" height="3"/><rect x="13" y="30" width="6" height="6"/></g></svg>
    <h3>BUSINESS</h3>
    <p>Here at Brambleoak Custom Cabinets we are proud to be involved in the custom cabinet market.</p>
    <div class="read-more">Read More <svg width="9" height="9" viewBox="0 0 10 10"><circle cx="5" cy="5" r="4.3" stroke="#fff" fill="none"/><path d="M5 2.5v5M2.5 5h5" stroke="#fff"/></svg></div>
  </div>
</section>

<h2 class="section-title works-title">OUR <span>WORKS</span></h2>
<div class="filter-tabs"><span class="active">All</span><span class="t-res">Residential</span><span class="t-bus">Business</span></div>

<div class="work" style="left:37px;top:805px;background:linear-gradient(160deg,#2a2422,#4a403a 60%,#6a5448)" role="img" aria-label="Photo of dark floor-to-ceiling wall cabinets"></div>
<div class="work feature" style="left:206px;top:805px">
  <h4>Lorem ipsum dolor</h4>
  <p>Contantry popilar sit</p>
  <svg class="plus" width="16" height="16" viewBox="0 0 16 16"><circle cx="8" cy="8" r="7" stroke="#fff" stroke-width="1.3" fill="none"/><path d="M8 4v8M4 8h8" stroke="#fff" stroke-width="1.5"/></svg>
  <svg class="fold" width="22" height="22" viewBox="0 0 22 22"><path d="M22 0L0 22h22z" fill="#f2f2f2"/><path d="M22 0L0 22V0z" fill="#a8300f"/></svg>
</div>
<div class="work" style="left:375px;top:805px;background:linear-gradient(180deg,#c8c8b8,#8a7a60 55%,#4a3a2c)" role="img" aria-label="Photo of a dining nook with window seat and dark table"></div>
<div class="work" style="left:543px;top:805px;background:linear-gradient(180deg,#8a8078,#3a302a 50%,#5a4636)" role="img" aria-label="Photo of a kitchen with dark island and stainless appliances"></div>
<div class="work" style="left:37px;top:920px;background:linear-gradient(180deg,#8a8a84,#5a4c40 55%,#3a2a20)" role="img" aria-label="Photo of a bright kitchen with white cabinets and bar seating"></div>
<div class="work" style="left:206px;top:920px;background:linear-gradient(180deg,#b0aca4,#7a5a48 50%,#2a2220)" role="img" aria-label="Photo of a kitchen island with pendant light"></div>
<div class="work" style="left:375px;top:920px;background:linear-gradient(180deg,#d8d4cc,#3a2e28 40%,#2a221e 80%,#c8c0b4)" role="img" aria-label="Photo of a dark entertainment wall unit"></div>
<div class="work" style="left:543px;top:920px;background:linear-gradient(180deg,#9a8a78,#4a3a30 55%,#6a4a30)" role="img" aria-label="Photo of an open kitchen with island and wood floor"></div>

<div class="pager"><i class="on"></i><i></i><i></i></div>

<footer class="site-footer">
  <nav class="footer-nav">
    <span class="home">Home</span>
    <span class="gallery">Gallery</span><span class="sep">|</span>
    <span>Services</span><span class="sep">|</span>
    <span>Warranty</span><span class="sep">|</span>
    <span>Contact</span>
  </nav>
  <div class="social"><i></i><i></i><i></i><i></i></div>
  <div class="social-tip">PORTFOLIO</div>
  <div class="divider"></div>

  <div class="contact-item" style="left:37px">
    <span class="ico"><svg width="7" height="9" viewBox="0 0 7 9"><path d="M3.5 0a3.2 3.2 0 0 0-3.2 3.2C.3 5.6 3.5 9 3.5 9s3.2-3.4 3.2-5.8A3.2 3.2 0 0 0 3.5 0zm0 4.4a1.2 1.2 0 1 1 0-2.4 1.2 1.2 0 0 1 0 2.4z" fill="#1c1c1c"/></svg></span>
    <span>4120 Township Road 517<br>Cedar Hollow, Alberta<br>T0M 2K4</span>
  </div>
  <div class="contact-item" style="left:164px">
    <span class="ico"><svg width="9" height="9" viewBox="0 0 9 9"><path d="M2 .5l1.4 2-1 1a5 5 0 0 0 3 3l1-1 2 1.4-.8 1.4C4 8.5.5 5 .6 1.3z" fill="#1c1c1c"/></svg></span>
    <span>555-310-4827<br>555-310-4830</span>
  </div>
  <div class="contact-item" style="left:251px">
    <span class="ico"><svg width="9" height="7" viewBox="0 0 9 7"><rect width="9" height="7" rx="1" fill="#1c1c1c"/><path d="M.5 1l4 3 4-3" stroke="#f0f0f0" fill="none" stroke-width=".9"/></svg></span>
    <span>sales@brambleoakcustomcabinets.com</span>
  </div>
  <div class="copyright">©Copyright 2015 yoursite. All Rights Reserved.</div>
</footer>

</body>
</html>
```